Business Card Design for Flood Rescue 360 - Property Restoration Professionals

I need a business card designed for Flood Rescue 360. We are a full-service property restoration solution. Providing water, fire, smoke & storm restoration as well as mold remediation and full remodel or reconstruction to homes and businesses across Dallas-Fort Worth, TX.
Target Market(s)
home and business owners with insurance covered property damage from water, fire or storm related damage
Industry/Entity Type
property restoration
Contact Information for Business Card
Marcus Pelley General Manager Cell: 214-555-0193 Office: 469-555-0148 email: Marcus@FloodRescue360.example services: Water, Fire, Mold, Reconstruction Tagline: Fast Help When the Water Rises!
Look and feel
Each slider illustrates characteristics of the customer's brand and the style your logo design should communicate.

```html
<!DOCTYPE html>
<html lang="en">
<head>
<meta charset="utf-8">
<title>Flood Rescue 360 – Business Card</title>
<link href="https://fonts.googleapis.com/css2?family=Roboto:wght@400;500;700;900&display=swap" rel="stylesheet">
<style>
  :root {
    --stage: #111111;
    --card: #efefef;
    --blue: #17b1e6;
    --gray: #7a7a7a;
    --ink: #1c1c1c;
    --emboss: #e4e4e4;
  }
  * { margin: 0; padding: 0; box-sizing: border-box; }
  html, body { width: 1200px; height: 960px; overflow: hidden; background: var(--stage); }
  body { position: relative; font-family: "Roboto", sans-serif; }

  .card {
    position: absolute; top: 130px; width: 400px; height: 700px;
    background: var(--card); border-radius: 26px; overflow: hidden;
  }
  .card--front { left: 173px; }
  .card--back { left: 628px; }

  /* front */
  .brand-ring {
    position: absolute; left: 118px; top: 120px; width: 140px; height: 140px;
    border: 10px solid var(--blue); border-radius: 50%;
  }
  .brand-vertical {
    position: absolute; left: 189px; top: 429px;
    transform: translate(-50%, -50%) rotate(-90deg);
    font-weight: 900; color: var(--blue); font-size: 60px; line-height: 58px;
    text-transform: uppercase; white-space: nowrap; text-align: left;
  }
  .services {
    position: absolute; left: 350px; top: 478px;
    transform: translate(-50%, -50%) rotate(-90deg);
    width: 340px; white-space: nowrap;
  }
  .services__head {
    display: flex; align-items: center; gap: 6px;
    color: var(--blue); font-size: 17px; letter-spacing: 0.5px;
  }
  .services__head .rule { flex: 1; height: 2px; background: var(--blue); }
  .services__head .rule--short { flex: 0 0 105px; }
  .services__list {
    margin-top: 4px; font-size: 17px; color: var(--ink); letter-spacing: 0.5px;
    display: flex; align-items: center; gap: 6px;
  }
  .services__list .dot {
    width: 10px; height: 10px; border-radius: 50%;
    border: 2px solid var(--blue); display: inline-block;
  }

  /* back */
  .brand-top {
    position: absolute; left: 199px; top: 128px; transform: translate(-50%, -50%);
    text-align: center; font-weight: 900; color: var(--blue);
    font-size: 38px; line-height: 42px; text-transform: uppercase; white-space: nowrap;
  }
  .brand-faint {
    position: absolute; left: 328px; top: 290px;
    transform: translate(-50%, -50%) rotate(-90deg);
    font-weight: 900; color: var(--emboss); font-size: 62px; line-height: 58px;
    text-transform: uppercase; white-space: nowrap;
  }
  .person { position: absolute; left: 0; right: 0; top: 432px; text-align: center; }
  .person__name { font-size: 34px; line-height: 40px; color: var(--gray); font-weight: 400; }
  .person__name strong { color: var(--blue); font-weight: 700; }
  .person__role { font-size: 17px; color: var(--ink); letter-spacing: 0.6px; margin-top: 2px; }

  .icon-row {
    position: absolute; left: 93px; top: 500px; width: 212px; height: 32px;
    display: flex; align-items: center; gap: 8px;
  }
  .icon-row .rule { flex: 1; height: 2px; background: var(--blue); }
  .icon-row svg { width: 30px; height: 30px; }

  .contact {
    position: absolute; left: 0; right: 0; top: 537px; text-align: center;
    font-size: 17px; line-height: 24px; color: var(--ink); letter-spacing: 0.9px;
  }
  .tagline {
    position: absolute; left: 45px; top: 638px; width: 308px; height: 35px;
    border: 2px solid var(--blue); color: var(--blue);
    font-size: 17px; display: flex; align-items: center; justify-content: center;
    letter-spacing: 0.3px;
  }
</style>
</head>
<body>

<section class="card card--front">
  <div class="brand-ring"></div>
  <div class="brand-vertical">Flood<br>Rescue<br>360</div>
  <div class="services">
    <div class="services__head">
      <span class="rule"></span><span>SERVICES</span><span class="rule rule--short"></span>
    </div>
    <div class="services__list">
      <span class="dot"></span>Water <span class="dot"></span>Fire <span class="dot"></span>Mold <span class="dot"></span>Reconstruction
    </div>
  </div>
</section>

<section class="card card--back">
  <div class="brand-faint">Flood<br>Rescue</div>
  <div class="brand-top">Flood Rescue<br>360</div>

  <div class="person">
    <div class="person__name"><strong>Marcus</strong> Pelley</div>
    <div class="person__role">General Manager</div>
  </div>

  <div class="icon-row">
    <span class="rule"></span>
    <svg viewBox="0 0 30 30" aria-label="Cell phone">
      <rect x="5" y="5" width="20" height="20" rx="3" transform="rotate(45 15 15)" fill="var(--blue)"/>
      <rect x="11.5" y="8.5" width="7" height="13" rx="1.2" fill="none" stroke="#fff" stroke-width="1.5"/>
    </svg>
    <svg viewBox="0 0 30 30" aria-label="Office phone">
      <rect x="5" y="5" width="20" height="20" rx="3" transform="rotate(45 15 15)" fill="var(--blue)"/>
      <path d="M10.5 11.5c0.5 3.5 4 7.5 7.8 8.2l1.6-1.9-2.2-1.5-1.1 1c-1.6-0.8-2.9-2.2-3.6-3.8l1-1.1-1.5-2.2z" fill="#fff"/>
    </svg>
    <svg viewBox="0 0 30 30" aria-label="Email">
      <rect x="5" y="5" width="20" height="20" rx="3" transform="rotate(45 15 15)" fill="var(--blue)"/>
      <rect x="9.5" y="11" width="11" height="8" fill="none" stroke="#fff" stroke-width="1.4"/>
      <path d="M9.5 11l5.5 4.5 5.5-4.5" fill="none" stroke="#fff" stroke-width="1.4"/>
    </svg>
    <span class="rule"></span>
  </div>

  <div class="contact">
    214-555-0193 (Cell)<br>
    469-555-0148 (Office)<br>
    Marcus@FloodRescue360.example
  </div>

  <div class="tagline">Fast Help When the Water Rises!</div>
</section>

</body>
</html>
```